New business card/stationary for a consulting company

I am looking for a clean and very professional looking business card for my consulting company as well as corresponding stationary. I am uploading our logo. I like simple and powerful for the feel. No graphics but I am open on everything else. Below is my contact information but would like the final to be in a version I can add my employees information into and print. Thank you.

Daniel Whitcombe
dan@ferncliffadvisory.com
2870 North 9th Avenue, Summit Floor, Elm Ridge, Illinois 60531
www.ferncliffadvisory.com

Industry/Entity Type

Consulting

Contact Information for Business Card

Daniel Whitcombe
dan@ferncliffadvisory.com
www.ferncliffadvisory.com

Font styles to use
Serif
Sans Serif

Requirements
Must have
• Our logo and the business card details.
Nice to have
• our website www.ferncliffadvisory.com

```html
<!DOCTYPE html>
<html lang="en">
<head>
<meta charset="utf-8">
<title>Ferncliff Advisory — Business Card</title>
<link rel="stylesheet" href="https://fonts.googleapis.com/css2?family=Marcellus&family=Roboto:wght@400&display=swap">
<style>
  :root {
    --navy: #132d5e;
    --paper: #f3f3f3;
    --paper-shade: #e9e9e9;
    --backdrop: #e4e4e4;
    --ink: #2a2a2a;
    --white: #ffffff;
  }
  * { margin: 0; padding: 0; box-sizing: border-box; }
  html, body {
    width: 1200px;
    height: 576px;
    overflow: hidden;
    background: var(--backdrop);
  }
  .canvas {
    position: relative;
    width: 1200px;
    height: 576px;
  }
  .card {
    position: absolute;
    width: 484px;
    height: 291px;
    border-radius: 14px;
    overflow: hidden;
  }
  .card-front {
    left: 82px;
    top: 139px;
    background: var(--navy);
  }
  .card-back {
    left: 600px;
    top: 139px;
    background: linear-gradient(180deg, var(--white) 0%, var(--paper) 55%, var(--paper-shade) 100%);
  }
  .brand-mark {
    display: block;
    background: var(--white);
  }
  .front-mark {
    position: absolute;
    left: 214px;
    top: 104px;
    width: 56px;
    height: 56px;
  }
  .brand-name {
    font-family: "Marcellus", serif;
    font-weight: 400;
    letter-spacing: 0.06em;
    text-transform: uppercase;
    white-space: nowrap;
  }
  .front-name {
    position: absolute;
    left: 0;
    right: 0;
    top: 181px;
    text-align: center;
    color: var(--white);
    font-size: 25px;
    line-height: 1;
  }
  .brand-band {
    position: absolute;
    left: 0;
    right: 0;
    top: 41px;
    height: 61px;
    background: var(--navy);
    display: flex;
    align-items: center;
    justify-content: center;
    gap: 14px;
  }
  .band-mark {
    width: 28px;
    height: 28px;
  }
  .band-name {
    color: var(--white);
    font-size: 24px;
    line-height: 1;
  }
  .contact {
    position: absolute;
    left: 0;
    right: 0;
    top: 134px;
    text-align: center;
  }
  .contact-name {
    font-family: "Marcellus", serif;
    font-weight: 400;
    color: var(--navy);
    font-size: 17px;
    letter-spacing: 0.08em;
    text-transform: uppercase;
    line-height: 1;
    margin-bottom: 14px;
  }
  .contact-line {
    font-family: "Roboto", sans-serif;
    font-size: 12.5px;
    color: var(--ink);
    line-height: 20px;
  }
  .contact-address {
    margin-top: 7px;
    font-family: "Roboto", sans-serif;
    font-size: 12.5px;
    color: var(--ink);
    line-height: 20px;
    font-style: normal;
  }
</style>
</head>
<body>
<main class="canvas">
  <section class="card card-front" aria-label="Business card front">
    <span class="brand-mark front-mark"></span>
    <p class="brand-name front-name">Ferncliff Advisory</p>
  </section>

  <section class="card card-back" aria-label="Business card back">
    <header class="brand-band">
      <span class="brand-mark band-mark"></span>
      <p class="brand-name band-name">Ferncliff Advisory</p>
    </header>
    <div class="contact">
      <h1 class="contact-name">Daniel Whitcombe</h1>
      <p class="contact-line">dan@ferncliffadvisory.com</p>
      <p class="contact-line">www.ferncliffadvisory.com</p>
      <address class="contact-address">2870 North 9th Avenue, Summit<br>Floor, Elm Ridge, Illinois 60531</address>
    </div>
  </section>
</main>
</body>
</html>
```